Business card design for Automotive workshop

We need a business card for a new automotive repair and tyre shop called Keelstone Prime Automotive located in New Zealand. We are a clean, modern and fresh workshop and company.

Front needs to feature logo,
my name:
Marlo Fenwicke (director)

Address:
48 Tarn Lane
Harlow Bay 3592

Phone: 07 594 2713
Mobile: 027 451 9362
Email: office@keelstoneautomotive.example.nz
Website: keelstoneautomotive.example.nz

Back needs to feature an area to write down appointment details, date and time.

Also feature a list of jobs and work we do such as,
Vehicle Servicing
All Mechanical Repairs
Warrant of Fitness
Tyres & Wheel Alignments
Automotive Diagnostics
Automotive Parts & Supplies

```html
<!DOCTYPE html>
<html lang="en">
<head>
<meta charset="utf-8">
<title>Keelstone Prime Automotive – Business Card</title>
<link rel="stylesheet" href="https://fonts.googleapis.com/css2?family=Exo+2:wght@600&family=Oswald:wght@600&family=Roboto:wght@400;500&display=swap">
<style>
  :root {
    --stage: #6b727c;
    --stage-dark: #4a515b;
    --card-core: #2b2b2d;
    --card-edge: #0d0d0e;
    --red: #e3161f;
    --white: #ffffff;
    --ink-line: #555555;
    --rule: #6d6d6d;
  }
  * { box-sizing: border-box; margin: 0; padding: 0; }
  html, body { width: 1200px; height: 900px; overflow: hidden; }
  body {
    background: linear-gradient(90deg, var(--stage-dark), var(--stage));
    display: flex; flex-direction: column; align-items: center; justify-content: center;
    gap: 40px;
    font-family: "Roboto", sans-serif;
  }
  .card {
    position: relative;
    width: 660px; height: 377px;
    background: radial-gradient(ellipse at 50% 40%, var(--card-core), var(--card-edge) 75%);
    box-shadow: 0 14px 30px rgba(0,0,0,.35);
    overflow: hidden;
  }

  /* Back: brand + appointment box */
  .brand {
    position: absolute; top: 70px; right: 48px;
    display: flex; align-items: center; gap: 14px;
  }
  .brand-mark { width: 22px; height: 22px; background: var(--red); }
  .brand-name {
    font-family: "Roboto", sans-serif; font-weight: 500;
    font-size: 30px; letter-spacing: 1px; color: var(--white);
    text-transform: uppercase;
  }
  .appointment {
    position: absolute; left: 0; right: 0; bottom: 40px;
    height: 130px; background: var(--white);
    padding: 24px 40px;
    display: flex; flex-direction: column; justify-content: center; gap: 28px;
  }
  .appt-row { display: flex; align-items: baseline; gap: 10px; }
  .appt-label { color: var(--red); font-size: 18px; }
  .appt-line { flex: 1; border-bottom: 2px dotted var(--ink-line); height: 1px; }
  .appt-line.date { flex: 1.4; }

  /* Front: contact */
  .identity {
    position: absolute; top: 95px; left: 30px; width: 250px; text-align: right;
    font-family: "Oswald", sans-serif; font-weight: 600; text-transform: uppercase;
  }
  .person-name { color: var(--red); font-size: 30px; letter-spacing: .5px; line-height: 1.1; }
  .person-role { color: var(--white); font-size: 20px; letter-spacing: .5px; }
  .divider { position: absolute; top: 85px; left: 300px; width: 1px; height: 160px; background: var(--rule); }
  .contact {
    position: absolute; top: 88px; left: 322px; right: 24px;
    font-family: "Exo 2", sans-serif; font-weight: 600; color: var(--white);
    font-size: 14px; line-height: 1.5;
  }
  .address { margin-bottom: 6px; padding-left: 22px; }
  .contact-row { display: flex; align-items: center; gap: 8px; white-space: nowrap; }
  .contact-row svg { width: 14px; height: 14px; flex: none; }
  .services {
    position: absolute; left: 0; right: 0; bottom: 45px; height: 80px;
    background: var(--red); color: var(--white);
    display: flex; flex-direction: column; align-items: center; justify-content: center;
    font-size: 17px; line-height: 1.45;
  }
</style>
</head>
<body>

<section class="card card-back" aria-label="Card back">
  <div class="brand">
    <span class="brand-mark"></span>
    <span class="brand-name">Keelstone Prime Automotive</span>
  </div>
  <div class="appointment">
    <div class="appt-row">
      <span class="appt-label">Date:</span><span class="appt-line date"></span>
      <span class="appt-label">Time:</span><span class="appt-line"></span>
    </div>
    <div class="appt-row">
      <span class="appt-label">Date:</span><span class="appt-line date"></span>
      <span class="appt-label">Time:</span><span class="appt-line"></span>
    </div>
  </div>
</section>

<section class="card card-front" aria-label="Card front">
  <div class="identity">
    <p class="person-name">Marlo Fenwicke</p>
    <p class="person-role">Director</p>
  </div>
  <div class="divider"></div>
  <div class="contact">
    <p class="address">48 Tarn Lane<br>Harlow Bay 3592</p>
    <p class="contact-row">
      <svg viewBox="0 0 16 16"><path fill="#e3161f" d="M3 1l3 3-2 2c1 2 3 4 5 5l2-2 3 3-2 3C7 14 2 9 1 3z"/></svg>
      07 594 2713
    </p>
    <p class="contact-row">
      <svg viewBox="0 0 16 16"><rect x="4" y="1" width="8" height="14" rx="1.5" fill="none" stroke="#e3161f" stroke-width="1.6"/><circle cx="8" cy="12.5" r="1" fill="#e3161f"/></svg>
      027 451 9362
    </p>
    <p class="contact-row">
      <svg viewBox="0 0 16 16"><rect x="1" y="3" width="14" height="10" fill="#e3161f"/><path d="M1 3l7 6 7-6" fill="none" stroke="#111" stroke-width="1.3"/></svg>
      office@keelstoneautomotive.example.nz
    </p>
    <p class="contact-row">
      <svg viewBox="0 0 16 16"><circle cx="8" cy="8" r="6.5" fill="none" stroke="#e3161f" stroke-width="1.6"/><path d="M1.5 8h13M8 1.5c-3 3.5-3 9.5 0 13M8 1.5c3 3.5 3 9.5 0 13" fill="none" stroke="#e3161f" stroke-width="1.2"/></svg>
      www.keelstoneautomotive.example.nz
    </p>
  </div>
  <div class="services">
    <p>All Mechanical Repairs • Warrant of Fitness • Tyres &amp; Wheel Alignments</p>
    <p>Automotive Diagnostics • Automotive Parts &amp; Supplies</p>
  </div>
</section>

</body>
</html>
```